BrivoTerna. Lantern of the Steady Harvest. Business card

Professional business card for BrivoTerna (Lantern of the Steady Harvest)
My rationale: Strategy-> Execution-> Results-> Value that lead to the BrivoTerna name: We put the Lantern of the Steady Harvest.
We deliver value to our customers helping them at defining a good strategy (cyan arrow). 90% of well formulated strategies fail due to poor execution so we also consider strategical execution very important (green arrow). Due to the execution we obtain the results (blue arrow). Finally, the results provide feedback to redefine strategy, and the new strategy has to be executed and new results obtained providing new feedback and on and on. It's like a wheel that finally, must create corporate value: value for shareholders, staholders, employees, providers...-

Target Market(s)

CEOs and steering comitees , invewrnent funds

Industry/Entity Type

Business Consultant

Contact Information for Business Card

Teodoro Vinsquel
CEO & Founder
teodoro.vinsquel@brivoterna-example.com
Mobile: +34 655.803.912
www.brivoterna-example.com

Colors

Designer to choose colors to be used in the design.

Requirements
Nice to have
• Nice to hace the words: Strategy, execution, results
• Nice to vave the claim: Lantern of the Steady Harvest
• The three colors should be shown:
• cyan for STRATEGY
• green for EXECUTION
• blue for RESULTS
Should not have
• Complete black background

```html
<!DOCTYPE html>
<html lang="en">
<head>
<meta charset="utf-8">
<title>BrivoTerna – Business Card</title>
<link rel="stylesheet" href="https://fonts.googleapis.com/css2?family=Roboto:wght@400;500;700&display=swap">
<style>
  :root {
    --backdrop: #b5b5b5;
    --card: #f7f7f7;
    --strategy-cyan: #0aa8e6;
    --execution-green: #8dc63f;
    --results-blue: #0b2f94;
    --ink: #3a3a3a;
  }
  * { margin: 0; padding: 0; box-sizing: border-box; }
  html, body {
    width: 1200px;
    height: 750px;
    overflow: hidden;
    background: var(--backdrop);
    font-family: "Roboto", sans-serif;
  }
  .canvas { position: relative; width: 1200px; height: 750px; }
  .card {
    position: absolute;
    top: 232px;
    width: 490px;
    height: 282px;
    background: var(--card);
  }
  .card--front { left: 90px; }
  .card--back { left: 620px; }

  .flow-arrow { position: absolute; left: 0; width: 276px; height: 16px; }
  .flow-arrow--strategy { top: 53px; }
  .flow-arrow--execution { top: 142px; }
  .flow-arrow--results { top: 220px; }

  .holder-name {
    position: absolute;
    left: 37px;
    top: 84px;
    font-size: 19px;
    font-weight: 500;
    color: var(--results-blue);
  }
  .holder-role {
    position: absolute;
    left: 37px;
    top: 110px;
    font-size: 15.5px;
    color: var(--execution-green);
  }
  .contact {
    position: absolute;
    left: 37px;
    top: 173px;
    font-size: 12.5px;
    line-height: 17px;
    color: var(--ink);
    list-style: none;
  }

  .brand-name {
    position: absolute;
    left: 0;
    right: 0;
    top: 140px;
    text-align: center;
    font-size: 44px;
    font-weight: 700;
    letter-spacing: -1px;
    color: var(--results-blue);
  }
  .web-address {
    position: absolute;
    left: 0;
    right: 0;
    top: 236px;
    text-align: center;
    font-size: 11px;
    font-weight: 500;
    letter-spacing: 4.5px;
  }
  .web-address .prefix { color: var(--results-blue); }
  .web-address .domain { color: var(--execution-green); }
  .web-address .suffix { color: var(--strategy-cyan); }
</style>
</head>
<body>
<main class="canvas">
  <section class="card card--front" aria-label="Card front">
    <svg class="flow-arrow flow-arrow--strategy" viewBox="0 0 276 16" aria-hidden="true">
      <rect x="0" y="6.5" width="264" height="3" fill="var(--strategy-cyan)"/>
      <polygon points="262,0 276,8 262,16" fill="var(--strategy-cyan)"/>
    </svg>
    <h1 class="holder-name">Teodoro Vinsquel</h1>
    <p class="holder-role">CEO &amp; Founder</p>
    <svg class="flow-arrow flow-arrow--execution" viewBox="0 0 276 16" aria-hidden="true">
      <rect x="0" y="6.5" width="264" height="3" fill="var(--execution-green)"/>
      <polygon points="262,0 276,8 262,16" fill="var(--execution-green)"/>
    </svg>
    <ul class="contact">
      <li>+34 655.803.912</li>
      <li>teodoro.vinsquel@brivoterna-example.com</li>
    </ul>
    <svg class="flow-arrow flow-arrow--results" viewBox="0 0 276 16" aria-hidden="true">
      <rect x="0" y="6.5" width="264" height="3" fill="var(--results-blue)"/>
      <polygon points="262,0 276,8 262,16" fill="var(--results-blue)"/>
    </svg>
  </section>

  <section class="card card--back" aria-label="Card back">
    <p class="brand-name">BrivoTerna</p>
    <p class="web-address"><span class="prefix">www.</span><span class="domain">brivoterna-example</span><span class="suffix">.com</span></p>
  </section>
</main>
</body>
</html>
```